Corvane Capital Business Cards

These are professional business cards that are for my family office.
Put fake emails and phone numbers as of now until I finalize those components. This family office controls my families investments, assets, and future. The cards should be professional.
..
.
.
.
I just uploaded another variation of a logo I would like to see as a business card to I am inbeteen which logo to use

Target Market(s)

business

Industry/Entity Type

business

Contact Information for Business Card

Professional, wealth related, finance related.

Requirements
Must have
• Logo

```html
<!DOCTYPE html>
<html lang="en">
<head>
<meta charset="utf-8">
<title>Corvane Capital Business Cards</title>
<link href="https://fonts.googleapis.com/css2?family=Montserrat:wght@400;600&display=swap" rel="stylesheet">
<style>
  :root {
    --backdrop: #e9e6e1;
    --card: #1b2030;
    --white: #ffffff;
    --name-grey: #a3a7b0;
    --body-text: #e4e6ea;
    --icon: #c9ccd3;
    --accent: #3d4f8f;
    --emboss: #141826;
  }
  * { margin: 0; padding: 0; box-sizing: border-box; }
  html, body { width: 900px; height: 1200px; overflow: hidden; }
  body {
    background: var(--backdrop);
    font-family: "Montserrat", Arial, sans-serif;
    position: relative;
  }
  .card {
    position: absolute;
    background: var(--card);
    border-radius: 24px;
    box-shadow: 0 6px 16px rgba(0,0,0,0.25);
    overflow: hidden;
  }
  .card-front { left: 80px; top: 130px; width: 742px; height: 442px; }
  .card-back { left: 78px; top: 638px; width: 744px; height: 440px; }

  .brand {
    position: absolute;
    display: flex;
    align-items: center;
    gap: 12px;
    font-weight: 600;
    text-transform: uppercase;
    letter-spacing: 2px;
    white-space: nowrap;
  }
  .brand-front { left: 37px; top: 68px; font-size: 32px; color: var(--white); }
  .brand-back { left: 72px; top: 208px; font-size: 50px; color: var(--emboss); }
  .brand-dot { width: 12px; height: 12px; border-radius: 50%; background: var(--accent); }
  .brand-back .brand-dot { width: 16px; height: 16px; }

  .holder { position: absolute; left: 37px; top: 188px; }
  .holder-name { font-size: 26px; font-weight: 600; color: var(--name-grey); line-height: 32px; }
  .holder-role { font-size: 16px; color: var(--body-text); line-height: 22px; }

  .address {
    position: absolute; left: 38px; top: 270px;
    font-size: 17px; line-height: 21px; color: var(--body-text);
  }
  .contacts { position: absolute; left: 37px; top: 330px; list-style: none; }
  .contact-item {
    display: flex; align-items: center; gap: 8px;
    font-size: 17px; color: var(--body-text); height: 28px;
  }
  .contact-icon { width: 15px; height: 15px; fill: var(--icon); flex: none; }
</style>
</head>
<body>
  <section class="card card-front">
    <div class="brand brand-front">Corvane Capital<span class="brand-dot"></span></div>

    <div class="holder">
      <p class="holder-name">Marcus Ellery</p>
      <p class="holder-role">Owner</p>
    </div>

    <p class="address">240 Linden Court Plaza<br>Harwick, NJ 07412 USA</p>

    <ul class="contacts">
      <li class="contact-item">
        <svg class="contact-icon" viewBox="0 0 24 24"><path d="M6.6 10.8a15 15 0 0 0 6.6 6.6l2.2-2.2a1 1 0 0 1 1-.25 11.4 11.4 0 0 0 3.6.57 1 1 0 0 1 1 1V20a1 1 0 0 1-1 1A17 17 0 0 1 3 4a1 1 0 0 1 1-1h3.5a1 1 0 0 1 1 1c0 1.25.2 2.45.57 3.6a1 1 0 0 1-.25 1z"/></svg>
        (555)214-7390
      </li>
      <li class="contact-item">
        <svg class="contact-icon" viewBox="0 0 24 24"><path d="M2 5h20v14H2z M2 5l10 7 10-7" fill="none" stroke="#c9ccd3" stroke-width="0"/><path d="M2 6.5 12 13l10-6.5V19H2z M2 5h20L12 11.5z"/></svg>
        info@yourwebsitename.com
      </li>
      <li class="contact-item">
        <svg class="contact-icon" viewBox="0 0 24 24"><circle cx="12" cy="12" r="10"/><path d="M2 12h20M12 2c3 3 3 17 0 20M12 2c-3 3-3 17 0 20" fill="none" stroke="#1b2030" stroke-width="1.5"/></svg>
        www.yourwebsitename.com
      </li>
    </ul>
  </section>

  <section class="card card-back">
    <div class="brand brand-back">Corvane Capital<span class="brand-dot"></span></div>
  </section>
</body>
</html>
```